Website development company website

ABOUT COMPANY
Hi everyone! We're a Melbourne, Australia website development company in a need of a website design that will make online store merchants want to engage our services.
We specialise exclusively in Torvista e-commerce platform (https://torvista-platform.example/). What distinguishes our business from competition is that rather than designing and building brand new websites, we offer development, support and maintenance services to established websites. Maintenance and Support are the keywords representing our business.
Our potential clients are people with broken, slow and underperforming Torvista installations who need assistance getting their websites up and making sales. Our website must pass the message that we can help, and provide quick means of making contact.
DESIGN
Overall, we're looking for a slick, clean, airy, conservative design. No need to do anything crazy, try to stick to what's "standard" in website design these days and make it easy on all of us. The website is unlikely to be updated too often so it needs to look attractive and fresh first time over and after a year, too.
Attached is our new logo, which you'll be able to take the basic idea from, the colors and fonts. Though, don't use the fonts from the logo in the website, stick to the standard widely supported fonts. Additional use of Google fonts is fine.
Don't overdo it with colors, stick to conservative basic color set and only use the colors from the log for accents like headings etc. Please, don't be tempted to use the blue and orange as background of whole blocks, other than perhaps footer. Thanks.
For the images used, I'd like to stay away from a design studio/digital agency feel and lean more towards professional support and maintenance services. I'm thinking images of content merchants doing their job. Something along the lines of "We'll be taking care of the website so that you only need to care about the business".
Some ideas I like:
http://www.plumframe-pics.example/detail/photo/portrait-of-confident-male-design-professional-royalty-free-image/572048163
http://www.plumframe-pics.example/detail/photo/designer-taking-picture-of-hat-high-res-stock-photography/839207514
http://www.plumframe-pics.example/detail/photo/woman-packaging-pottery-royalty-free-image/216684093
Images of colorful shopping bags and shopping carts are over the top and not serious enough. Instead of images matching Online Shopping, I'd try going more for Stability, Reliability, Performance.
Our existing website is http://www.bravuln.example. Please, don't take design ideas from it, but it will give you a picture of the structure of our new website and content that's going to be used initially.
If you could include a basic icon set to use throughout the website, that would be great. If the icons could match our logo (attached), it would be a big plus.
ALL PAGES
Every page must contain clearly visible phone number (1300 648 907) and a Contact Us Now button, which opens an AJAX driven popup form with Name, Email, Phone and Message to be sent through.
To start with, main menu items will be Torvista, Portfolio, Contact.
At the bottom of each page, please, include a newsletter subscription form with text Subscribe to Torvista Support and Security Updates.
For the footer, I'd like to see a logo strip with the following logos in grayscale (no need to link anywhere): Torvista, QRX, DataVane, NCB. You'll find the logos on Google Images.
Standard footer columns follow. Here, I'd like to see logos in color: Torvista Certified Developer, Torvista Ceritified Solution Provider. Again, the logos are on Google Images.
No social media logos/links necessary anywhere on the website.
...and then the copyright line.
FRONT PAGE
Large slider with images that would appeal to our target audience. Keywords here would be Torvista System Audit, Torvista Performance Optimisation, Torvista Website Emergency Recovery, Torvista Development Infrastructure Hosting. We'll have a static page created for each of these to link to.
In a corner of the slider, or on the edge, can I have an overlay with logos in color (same as footer): Torvista Certified Developer, Torvista Ceritified Solution Provider.
Underneath, a number of blocks, each with an image and teaser that we'll use to link to various pages throughout the website.
PORTFOLIO PAGE
I'm thinking a single long page with a block per client, which will contain project name, description from us and a testimonial from client. Also, each block will contain a single large screenshot. No gallery or slideshow is necessary here, just one image per project.
I'll leave the layout up to you, but try to put yourself in the shoes of a potential client reviewing our past work by simply scrolling down this one page.
CONTACT US PAGE
Separate page with the same form as above, phone number (1300 648 907), email address (support@kavreo.example), address (Suite 42, Level 3|8 Wattlebrook Lane|Fernvale Heights VIC 3999), and a grayscale Google Map.
CODING UP
Coding up into static HTML/CSS/JS is equally important as the design itself. We're a website development company, we'll be integrating the theme. We will spot any issues and we will point them out.
Coded up design must be fully responsive. Enough said.
To be able to create any content in future, we'd like one extra page coded up with samples of all themed elements, lists, forms, buttons, 2, 3, 4-column layout, alerts, icons, etc. This page does not need to be designed, only coded up.
The design will be integrated into Drupal using Twig. If possible at all, try to keep it in mind when designing and coding up, and make the integration into a Drupal theme easier for us.
GOOD LUCK!
That's it. Let me know if anything needs clarifying. So far I've had a great experience with ArtFlockly. I don't doubt some great designs will emerge. Clever ideas are highly appreciated, but also make it clear you've read and followed the points in this brief. Cheers, Tom

```html
<!DOCTYPE html>
<html lang="en">
<head>
<meta charset="utf-8">
<title>Contact – Kavreo E-Commerce</title>
<link href="https://fonts.googleapis.com/css2?family=Open+Sans:ital,wght@0,400;0,600;0,700;1,400&display=swap" rel="stylesheet">
<style>
:root{
  --blue:#0c3b6e;
  --blue-dark:#082b52;
  --orange:#e8791f;
  --orange-light:#f29a4a;
  --text:#555;
  --heading:#444;
  --line:#d6d6d6;
  --map:#d9d9d9;
  --strip:#efefef;
}
*{box-sizing:border-box;margin:0;padding:0}
html,body{width:789px;height:1200px;overflow:hidden}
body{position:relative;font-family:"Open Sans",Arial,sans-serif;color:var(--text);background:#fff}
.abs{position:absolute}
.topbar{left:0;top:0;width:789px;height:18px;background:var(--blue)}
.topbar-phone{left:106px;top:2px;height:14px;padding:0 5px 0 2px;border:1px solid #fff;border-radius:3px;color:#fff;font-size:8px;display:flex;align-items:center;gap:4px}
.topbar-phone i{width:10px;height:10px;border-radius:50%;background:var(--orange);display:flex;align-items:center;justify-content:center}
.topbar-cta{right:106px;top:4px;color:#fff;font-size:8px;display:flex;align-items:center;gap:3px}
.header{left:0;top:18px;width:789px;height:41px;background:#fff;border-bottom:1px solid #eee}
.brand{left:106px;top:27px;display:flex;align-items:center;gap:5px;color:var(--blue);font-weight:700;font-size:17px}
.brand span{width:14px;height:14px;background:var(--orange)}
.nav{right:106px;top:35px;display:flex;gap:16px;font-size:7.5px;color:#444}
.nav .active{border-bottom:1.5px solid var(--orange);padding-bottom:6px}
.banner{left:0;top:59px;width:789px;height:52px;background:linear-gradient(90deg,#ea6f1a,var(--orange-light) 50%,#ea6f1a)}
.banner h1{position:absolute;left:105px;top:18px;font-weight:400;font-size:15px;color:#fff}
.crumbs{right:106px;top:23px;color:#fff;font-size:7.5px}
.title{left:0;width:789px;text-align:center;font-size:12px;font-weight:400;color:var(--heading)}
.divider{left:352px;width:85px;height:10px}
.card{top:168px;width:184px;height:160px;border:1px solid var(--line);text-align:center}
.card .icon{width:66px;height:65px;margin:25px auto 0;background:var(--orange);display:flex;align-items:center;justify-content:center}
.card h3{margin-top:20px;font-size:8.5px;font-weight:700;color:#444}
.card p{margin-top:3px;font-size:7px;line-height:10px}
.label{font-size:8px;color:#555}
.field{border:1px solid var(--line);background:#fff;box-shadow:inset 0 1px 2px rgba(0,0,0,.06)}
.note{left:0;top:541px;width:789px;text-align:center;font-size:7px;font-style:italic}
.note em{color:#d33}
.btn{background:var(--orange);color:#fff;font-size:7px;font-weight:600;display:flex;align-items:center;justify-content:center}
.map{left:0;top:605px;width:789px;height:260px;background:linear-gradient(135deg,#e0e0e0,var(--map) 50%,#e3e3e3)}
.strip{left:0;top:890px;width:789px;height:92px;background:linear-gradient(#f6f6f6,var(--strip) 50%,#f6f6f6);display:flex;justify-content:space-around;align-items:center;padding:0 90px}
.strip span{font-size:20px;font-weight:700;color:#6e6e6e}
.footer{left:0;top:1009px;width:789px;height:163px;background:var(--blue);color:#fff}
.fcol{top:1018px;width:180px;font-size:7px;line-height:10px;color:#fff}
.fcol h4{font-size:8px;font-weight:700;display:inline-block;border-bottom:1.5px solid #fff;margin-bottom:9px;padding-bottom:1px}
.about p{text-align:justify}
.badges{display:flex;gap:12px;margin-top:10px}
.badges span{width:29px;height:50px;background:var(--orange);border:2px solid #fff}
.crow{display:flex;align-items:center;gap:6px;margin:7px 0 0}
.crow i{width:13px;height:13px;border-radius:50%;background:var(--blue-dark);display:flex;align-items:center;justify-content:center}
.sub-input{width:147px;height:19px;background:#fff;border-radius:2px;margin-top:12px;color:#888;font-size:7px;padding:4px 6px}
.sub-btn{width:50px;height:19px;margin-top:11px}
.bottombar{left:0;top:1172px;width:789px;height:28px;background:var(--blue-dark);color:#fff;font-size:7px}
.bottombar nav{position:absolute;left:106px;top:10px;display:flex;gap:12px}
.bottombar small{position:absolute;right:106px;top:10px;font-size:7px}
</style>
</head>
<body>
<div class="abs topbar"></div>
<div class="abs topbar-phone"><i><svg width="6" height="6" viewBox="0 0 24 24"><path fill="#fff" d="M6.6 10.8a15 15 0 006.6 6.6l2.2-2.2c.3-.3.7-.4 1-.2 1.1.4 2.3.6 3.6.6.6 0 1 .4 1 1V20c0 .6-.4 1-1 1A17 17 0 013 4c0-.6.4-1 1-1h3.5c.6 0 1 .4 1 1 0 1.3.2 2.5.6 3.6.1.3 0 .7-.2 1z"/></svg></i>1300 648 907</div>
<div class="abs topbar-cta"><svg width="8" height="7" viewBox="0 0 16 14"><path fill="#fff" d="M2 1h9a2 2 0 012 2v4a2 2 0 01-2 2H6l-3 3V9H2a2 2 0 01-2-2V3a2 2 0 012-2z"/></svg>Contact Us Now</div>

<header class="abs header"></header>
<div class="abs brand"><span></span>Kavreo</div>
<nav class="abs nav"><span>HOME</span><span>TORVISTA</span><span>PORTFOLIO</span><span class="active">CONTACT</span></nav>

<section class="abs banner"><h1>CONTACT</h1><div class="abs crumbs">HOME &nbsp;»&nbsp; CONTACT</div></section>

<h2 class="abs title" style="top:123px">GET IN TOUCH</h2>
<svg class="abs divider" style="top:142px" viewBox="0 0 85 10"><line x1="0" y1="5" x2="34" y2="5" stroke="#e8791f"/><line x1="51" y1="5" x2="85" y2="5" stroke="#e8791f"/><circle cx="42.5" cy="5" r="4" fill="none" stroke="#e8791f" stroke-width="1.2"/></svg>

<div class="abs card" style="left:105px"><div class="icon"><svg width="28" height="38" viewBox="0 0 24 32"><path fill="#fff" d="M12 0a12 12 0 00-12 12c0 9 12 20 12 20s12-11 12-20A12 12 0 0012 0zm0 17a5 5 0 110-10 5 5 0 010 10z"/></svg></div><h3>OUR ADDRESS</h3><p>Suite 42, Level 3, 8 Wattlebrook Lane<br>Fernvale Heights VIC 3999</p></div>
<div class="abs card" style="left:302px"><div class="icon"><svg width="36" height="36" viewBox="0 0 24 24"><path fill="#fff" d="M6.6 10.8a15 15 0 006.6 6.6l2.2-2.2c.3-.3.7-.4 1-.2 1.1.4 2.3.6 3.6.6.6 0 1 .4 1 1V20c0 .6-.4 1-1 1A17 17 0 013 4c0-.6.4-1 1-1h3.5c.6 0 1 .4 1 1 0 1.3.2 2.5.6 3.6.1.3 0 .7-.2 1z"/></svg></div><h3>TELEPHONE</h3><p>1300 648 907</p></div>
<div class="abs card" style="left:500px"><div class="icon"><svg width="46" height="34" viewBox="0 0 46 34"><rect x="1" y="1" width="44" height="32" rx="4" fill="#fff"/><path d="M4 5l19 14L42 5" fill="none" stroke="#e8791f" stroke-width="3"/></svg></div><h3>EMAIL</h3><p>support@kavreo.example</p></div>

<h2 class="abs title" style="top:342px">LEAVE A MESSAGE</h2>
<svg class="abs divider" style="top:361px" viewBox="0 0 85 10"><line x1="0" y1="5" x2="34" y2="5" stroke="#e8791f"/><line x1="51" y1="5" x2="85" y2="5" stroke="#e8791f"/><circle cx="42.5" cy="5" r="4" fill="none" stroke="#e8791f" stroke-width="1.2"/></svg>

<form>
<label class="abs label" style="left:106px;top:378px">NAME</label>
<div class="abs field" style="left:106px;top:390px;width:181px;height:27px"></div>
<label class="abs label" style="left:303px;top:378px">EMAIL</label>
<div class="abs field" style="left:303px;top:390px;width:181px;height:27px"></div>
<label class="abs label" style="left:501px;top:378px">PHONE</label>
<div class="abs field" style="left:501px;top:390px;width:181px;height:27px"></div>
<label class="abs label" style="left:106px;top:430px">MESSAGE</label>
<div class="abs field" style="left:106px;top:443px;width:576px;height:92px"></div>
<p class="abs note"><em>* All fields are required.</em> Once we receive your message we will respond as soon as possible.</p>
<div class="abs btn" style="left:357px;top:565px;width:74px;height:21px">SEND MESSAGE</div>
</form>

<div class="abs map" role="img" aria-label="Grayscale street map showing the office location"></div>

<div class="abs strip"><span>Torvista</span><span>QRX</span><span>DataVane</span><span>NCB</span></div>

<footer class="abs footer"></footer>
<div class="abs fcol about" style="left:106px"><h4>ABOUT US</h4><p>Torvista, fully owned by Quellmart Inc., is one of the most popular eCommerce platforms. It offers flexible, scalable eCommerce solutions designed to help businesses grow and succeed online. The Torvista platform is trusted by more than 150,000 businesses, including some of the world's leading brands.</p><div class="badges"><span></span><span></span></div></div>
<div class="abs fcol" style="left:304px"><h4>ADDRESS</h4><p>Suite 42, Level 3, Ashcourt Building<br>8 Wattlebrook Lane<br>Fernvale Heights VIC 3999</p><h4 style="margin-top:6px;margin-bottom:0">PHONE</h4><div class="crow"><i><svg width="6" height="6" viewBox="0 0 24 24"><path fill="#fff" d="M6.6 10.8a15 15 0 006.6 6.6l2.2-2.2c.3-.3.7-.4 1-.2 1.1.4 2.3.6 3.6.6.6 0 1 .4 1 1V20c0 .6-.4 1-1 1A17 17 0 013 4c0-.6.4-1 1-1h3.5c.6 0 1 .4 1 1 0 1.3.2 2.5.6 3.6.1.3 0 .7-.2 1z"/></svg></i>1300 274 516</div><h4 style="margin-top:8px;margin-bottom:0">EMAIL ID</h4><div class="crow"><i><svg width="7" height="5" viewBox="0 0 14 10"><rect width="14" height="10" fill="#fff"/><path d="M0 0l7 5 7-5" fill="none" stroke="#082b52"/></svg></i>support@kavreo.example</div></div>
<div class="abs fcol" style="left:502px"><h4>NEWSLETTER SUBSCRIPTION</h4><p>Subscribe to Torvista Support and Security Updates.</p><div class="sub-input">Email id</div><div class="btn sub-btn">SUBSCRIBE</div></div>

<div class="abs bottombar"><nav><span>HOME</span><span>TORVISTA</span><span>PORTFOLIO</span><span>CONTACT</span></nav><small>Copyright 2016 kavreo.example. All rights reserved</small></div>
</body>
</html>
```